Front and back cover design for skincare marketing materials

Thank you for showing an interest in my project.
Project Details.

I require a front and back cover for our marketing materials.
·       Front Cover size: 105 mm W x 150 mm H.
·       Back Cover size:  105 mm W x 150 mm H.
·       It must include these two colors. You can use a third color if you wish.
1.     #DBA09D
2.     #FFFFFF
 
Front Cover
·      The front cover will have a faded image of the Kakadu Plum branch and fruit. There are two image files, KP_image-1.jpg and kp_image-2.jpeg. You can use both images, just a portion of them, or source alternative royalty-free images of Kakadu Plum that may better fit the design. These two files have been uploaded.
 
The front cover wording.
Top of the front cover.
a.     The title of the image. “Kakadu Plum”
b.     The brand name, “Vellora Skincare”. The file brand_name.ai uploaded.
 
Bottom of the front cover- Designer's choice of font.
The bottom of the front cover contains three lines of text in the following order.  
1.     Australian Native Ingredients
2.     100% Natural · Organic · Wild-harvested
3.     Australian-Made Premium Skincare
 
Back Cover
·      Back Cover wording.The back cover contains the following words "grown by nature" in white (#FFFFFF) of font Italianno (font_file.ttf) with a background color of #DBA09D as seen in the sample box (sample_box.pdf) right-side panel
 
Please provide one file for the front cover and a separate file for the back cover.
All the elements of the files must be editable.
 
Do NOT use the Curve function on the files, as the text must remain editable/changeable.
 
All assets/resources/files, including fonts not supplied by us but used by the designer, must be named and provided with the finished design.
Updates

Slow to provide project details.

Target Market(s)

Beauty-minded Asian consumers between the ages of 32 and 75 who take a proactive approach to maintaining younger-looking skin. Those who already know the danger of skin damage caused by skincare containing harsh chemicals choose effective natural/organic solutions to meet their skincare needs. Those who wish a more radiant glow and youthful appearance to their skin. Usually, a two-income middle to high-income bracket couples with a mindset for health and beauty.

Industry/Entity Type

beauty

Font styles to use
Other font styles liked:
• I will provide a font file and a brand name file.

Requirements
Must have
• You must use the two colors provided on the product box. The designer may use a third color.
Nice to have
• some gold colour

```html
<!DOCTYPE html>
<html lang="en">
<head>
<meta charset="utf-8">
<title>Vellora Skincare – Kakadu Plum covers</title>
<link rel="stylesheet" href="https://fonts.googleapis.com/css2?family=Italianno&family=Poppins:wght@400&display=swap">
<style>
  :root {
    --brand-pink: #DBA09D;
    --white: #FFFFFF;
    --mist: #f4e6e3;
    --fruit-warm: #d9a88a;
    --rule: rgba(255,255,255,0.45);
    --page: #FFFFFF;
  }
  * { box-sizing: border-box; margin: 0; padding: 0; }
  html, body {
    width: 885px; height: 1200px; overflow: hidden;
    background: var(--page);
  }
  .spread {
    position: relative;
    width: 885px; height: 1200px;
    display: flex; align-items: center; justify-content: center;
    gap: 48px;
  }
  .cover {
    position: relative;
    width: 400px; height: 571px;
    overflow: hidden;
    box-shadow: 0 2px 8px rgba(0,0,0,0.12);
  }

  /* Front cover */
  .cover-front .photo-fill {
    position: absolute; inset: 0;
    background:
      radial-gradient(ellipse 55% 30% at 30% 70%, rgba(214,150,130,0.75), transparent 70%),
      radial-gradient(ellipse 45% 35% at 80% 60%, rgba(220,180,138,0.7), transparent 70%),
      radial-gradient(ellipse 40% 25% at 70% 85%, rgba(205,160,120,0.5), transparent 70%),
      linear-gradient(180deg, var(--mist) 0%, #f0dcd8 28%, #e2b4a8 50%, var(--fruit-warm) 72%, #d09a8e 100%);
  }
  .brand-name {
    position: absolute; top: 40px; left: 0; right: 0;
    text-align: center;
    font-family: "Italianno", cursive;
    font-weight: 400;
    font-size: 62px; line-height: 1;
    color: var(--brand-pink);
  }
  .product-title {
    position: absolute; left: 58px; top: 196px;
    font-family: "Italianno", cursive;
    font-weight: 400;
    color: var(--white);
    font-size: 100px; line-height: 0.82;
  }
  .product-title .line-two { display: block; padding-left: 110px; }
  .badge-row {
    position: absolute; left: 0; right: 0; bottom: 30px;
    display: flex; justify-content: center; align-items: center;
  }
  .badge {
    width: 92px; height: 56px;
    display: flex; align-items: center; justify-content: center;
  }
  .badge + .badge { border-left: 1px solid var(--rule); }
  .badge-disc {
    width: 48px; height: 48px; border-radius: 50%;
    background: var(--brand-pink);
  }

  /* Back cover */
  .cover-back { background: var(--brand-pink); }
  .cover-back .frame {
    position: absolute; inset: 19px 23px;
    border: 1px solid var(--white);
  }
  .tagline {
    position: absolute;
    left: 198px; top: 292px;
    transform: translate(-50%, -50%) rotate(-90deg);
    white-space: nowrap;
    font-family: "Italianno", cursive;
    font-weight: 400;
    font-size: 96px; line-height: 1;
    color: var(--white);
  }
</style>
</head>
<body>
  <main class="spread">
    <section class="cover cover-front" aria-label="Front cover">
      <div class="photo-fill" role="img" aria-label="Faded photograph of a Kakadu plum branch with fruit and leaves"></div>
      <div class="brand-name">Vellora Skincare</div>
      <h1 class="product-title">Kakadu<span class="line-two">Plum</span></h1>
      <div class="badge-row">
        <div class="badge"><span class="badge-disc"></span></div>
        <div class="badge"><span class="badge-disc"></span></div>
        <div class="badge"><span class="badge-disc"></span></div>
      </div>
    </section>

    <section class="cover cover-back" aria-label="Back cover">
      <div class="frame"></div>
      <p class="tagline">grown by nature</p>
    </section>
  </main>
</body>
</html>
```